Luxury Business Card Design for High-End Window Treatments

Gilded Slatworks
Custom Plantation Shutters & Architectural Shading Systems

⸻

BACK

Daniel Trevick
Owner

Custom Interior & Exterior Window Treatments

919-555-0148
gildedslatworks.com

I have included a picture that I’m hoping we can use on the back, but I’m also wondering if you can get rid of the ladder? Should we get rid of shutters , shades and blinds underneath Gilded Slatworks?

Target Market(s)

High-end residential homeowners, custom home builders, architects, interior designers, and luxury renovation clients seeking premium plantation shutters and motorized architectural shading systems.

Industry/Entity Type

Custom Window treatments

Contact Information for Business Card

Front Gilded Slatworks Custom Plantation Shutters Motorized Architectural Shading Systems BACK Daniel Trevick Owner 919-555-0148 GildedSlatworks.com Custom Interior & Exterior Window Treatments By Appointment

Requirements
Nice to have
• Not 100% sure on nice to halves or the color but you can definitely check out my website to get a better understanding of what I’m trying to do

```html
<!DOCTYPE html>
<html lang="en">
<head>
<meta charset="utf-8">
<title>Gilded Slatworks – Business Card</title>
<link href="https://fonts.googleapis.com/css2?family=Playfair+Display:wght@600&family=Mulish:wght@400;600&display=swap" rel="stylesheet">
<style>
  :root {
    --page: #e9e8ea;
    --ink: #0d0d0d;
    --gold: #bfab61;
    --gold-bright: #e3c766;
    --cream: #efe9d8;
    --white: #ffffff;
  }
  * { margin: 0; padding: 0; box-sizing: border-box; }
  html, body { width: 1200px; height: 1108px; overflow: hidden; background: var(--page); }
  .canvas { position: relative; width: 1200px; height: 1108px; }
  .card { position: absolute; overflow: hidden; }
  .card-back { left: 222px; top: 52px; width: 786px; height: 478px; background: var(--ink); }
  .card-front { left: 220px; top: 577px; width: 788px; height: 463px; }
  .backdrop-photo {
    position: absolute; inset: 0;
    background: linear-gradient(180deg, #141414 0%, #1c1c1a 55%, #232320 100%);
  }
  .wave { position: absolute; left: 0; top: 0; width: 786px; height: 478px; }
  .owner-name {
    position: absolute; left: 38px; top: 54px;
    font: 600 30px/1 "Playfair Display", serif; color: var(--gold);
  }
  .owner-role {
    position: absolute; left: 37px; top: 92px;
    font: 400 17px/1 "Mulish", sans-serif; color: var(--white);
  }
  .services {
    position: absolute; left: 40px; top: 158px;
    font: 400 17px/22px "Mulish", sans-serif; color: var(--white);
  }
  .contact { position: absolute; left: 38px; top: 254px; list-style: none; }
  .contact li {
    display: flex; align-items: center; gap: 10px; height: 29px;
    font: 400 18px/1 "Mulish", sans-serif; color: var(--white);
  }
  .contact svg { width: 18px; height: 18px; fill: var(--gold); }
  .appointment {
    position: absolute; left: 38px; top: 321px;
    font: 400 18px/1 "Mulish", sans-serif; color: var(--gold);
  }
  .brand-name {
    position: absolute; left: 400px; top: 128px; width: 320px; text-align: center;
    font: 600 56px/64px "Mulish", sans-serif; color: var(--cream);
  }
  .brand-tagline {
    position: absolute; left: 402px; top: 296px; width: 314px;
    display: flex; justify-content: space-between;
    font: 600 26px/1 "Mulish", sans-serif; color: var(--gold-bright);
  }
  .house-photo {
    position: absolute; inset: 0;
    background: linear-gradient(180deg, #7fb0e4 0%, #a9c8e6 22%, #2a2c33 40%, #2c2e36 52%, #d8d4ca 58%, #6b5d52 72%, #4b5a3a 86%, #8d8a72 100%);
  }
</style>
</head>
<body>
<main class="canvas">
  <section class="card card-back">
    <div class="backdrop-photo" role="img" aria-label="Darkened photo of a house porch with exterior shades, used as card background"></div>
    <svg class="wave" viewBox="0 0 786 478" aria-hidden="true">
      <path d="M0 388 C120 360 230 370 360 408 C480 442 600 470 700 440 C740 428 770 402 786 382 L786 478 L0 478 Z" fill="var(--gold)"/>
      <path d="M0 402 C140 368 260 378 400 420 C520 456 650 476 740 450 C760 444 775 436 786 428" fill="none" stroke="var(--ink)" stroke-width="6"/>
    </svg>
    <h1 class="owner-name">Daniel Trevick</h1>
    <p class="owner-role">Owner</p>
    <p class="services">Custom Interior &amp; Exterior<br>Window Treatments</p>
    <ul class="contact">
      <li><svg viewBox="0 0 24 24"><path d="M2 8c0-3 4-5 10-5s10 2 10 5v2h-5V8c-2-1-8-1-10 0v2H2zM6 11h12l3 9H3z"/></svg>919-555-0148</li>
      <li><svg viewBox="0 0 24 24"><path d="M12 2a10 10 0 1 0 0 20 10 10 0 0 0 0-20zm-1 3c-1 2-3 2-3 4s3 1 3 3-2 2-1 5c-3-1-5-4-5-7 0-2 2-5 6-5zm3 1c3 1 5 3 5 6 0 1 0 2-1 3-1-2-3-1-3-3s-2-2-1-6z"/></svg>GildedSlatworks.com</li>
    </ul>
    <p class="appointment">By Appointment</p>
    <p class="brand-name">Gilded<br>Slatworks</p>
    <p class="brand-tagline"><span>Shutters</span><span>Shades</span><span>Blinds</span></p>
  </section>
  <section class="card card-front">
    <div class="house-photo" role="img" aria-label="Photo of a brick home with a covered porch fitted with dark exterior shades, pine trees and blue sky behind, lawn chairs in front"></div>
  </section>
</main>
</body>
</html>
```